DESIGN OF STATIONERY - TORVALE MED

WE WORK IN THE FIELD OF HEALTH (IMAGING: MRI - CT ETC.).
WE WOULD LIKE TO CREATE THE ENTIRE STATIONERY DESIGN : LETTERHEAD, BUSINESS CARD, CALENDAR, INVOICES, CD HOLDER, ETC.

Target Market(s)

PERSONS UNDERTAKING HEALTH EXAMINATIONS

```html
<!DOCTYPE html>
<html lang="en">
<head>
<meta charset="utf-8">
<title>Torvale Med – Letterhead</title>
<link href="https://fonts.googleapis.com/css2?family=Open+Sans:wght@400;600&family=Roboto:wght@400&display=swap" rel="stylesheet">
<style>
  :root {
    --backdrop: #dcdcdc;
    --paper: #f8f8f8;
    --brand-blue: #1a6fb5;
    --brand-teal: #14a096;
    --ink: #4a4a4a;
    --ink-soft: #555555;
    --accent-wash-start: #e9f1ee;
    --accent-wash-end: #e7edf5;
    --signature-tone: #ececec;
  }
  * { margin: 0; padding: 0; box-sizing: border-box; }
  html, body {
    width: 1153px; height: 1200px; overflow: hidden;
    background: var(--backdrop);
  }
  .letterhead {
    position: absolute; left: 166px; top: 27px;
    width: 820px; height: 1146px;
    background: var(--paper);
    font-family: "Open Sans", sans-serif;
    color: var(--ink);
    overflow: hidden;
  }
  .brand-name {
    position: absolute; left: 73px; top: 72px;
    font-family: "Open Sans", sans-serif;
    font-weight: 600; font-size: 30px; letter-spacing: 0.2px;
    color: var(--brand-blue);
  }
  .header-rule { position: absolute; left: 0; top: 0; }
  .sender-address, .contact-list {
    position: absolute; left: 581px;
    font-family: "Roboto", sans-serif;
    font-size: 13px; line-height: 17px;
    color: var(--ink-soft);
  }
  .sender-address { top: 77px; font-style: normal; }
  .contact-list { top: 129px; list-style: none; }
  .contact-list li { display: flex; align-items: center; gap: 5px; height: 18px; }
  .contact-list svg { width: 13px; height: 13px; flex: none; }
  .letter-body {
    position: absolute; left: 73px; top: 267px; width: 664px;
    font-size: 15px; line-height: 22px;
  }
  .letter-body p { margin-bottom: 22px; text-align: justify; }
  .letter-body .salutation, .letter-body .closing { text-align: left; }
  .signature {
    position: absolute; left: 75px; top: 890px;
    width: 98px; height: 90px;
    background: var(--signature-tone);
  }
  .accent-area {
    position: absolute; left: 554px; top: 886px;
    width: 258px; height: 253px;
    background: linear-gradient(160deg, var(--accent-wash-start), var(--accent-wash-end));
  }
</style>
</head>
<body>
  <main class="letterhead">
    <div class="brand-name">Torvale Med</div>

    <svg class="header-rule" width="820" height="140" aria-hidden="true">
      <line x1="248" y1="117" x2="744" y2="117" stroke="var(--brand-teal)" stroke-width="3"/>
      <circle cx="744" cy="117" r="4.5" fill="var(--brand-teal)"/>
    </svg>

    <address class="sender-address">
      Harwick Court, 14 Elmfield<br>Rd, London SE4 7QN
    </address>

    <ul class="contact-list">
      <li>
        <svg viewBox="0 0 16 16"><path d="M3.5 1.5l2.5 3-1.5 1.5c.8 2 2.5 3.7 4.5 4.5L10.5 9l3 2.5-1.5 2.5C7 14 2 9 1.5 3z" fill="var(--brand-blue)"/></svg>
        0208 415 3962
      </li>
      <li>
        <svg viewBox="0 0 16 16"><rect x="1" y="3" width="14" height="10" fill="none" stroke="var(--brand-blue)" stroke-width="1.5"/><path d="M1 3l7 6 7-6M1 13l5-5M15 13l-5-5" fill="none" stroke="var(--brand-blue)" stroke-width="1.2"/></svg>
        info@torvalemed.com
      </li>
      <li>
        <svg viewBox="0 0 16 16"><g fill="none" stroke="var(--brand-blue)" stroke-width="1.1"><circle cx="8" cy="8" r="6.5"/><ellipse cx="8" cy="8" rx="3" ry="6.5"/><path d="M1.5 8h13M2.5 4.5h11M2.5 11.5h11"/></g></svg>
        www.torvalemed.com
      </li>
    </ul>

    <section class="letter-body">
      <p class="salutation">Dear customer,</p>
      <p>Lorem ipsum dolor sit amet, consectetur adipisicing elit, sed do eiusmod tempor incididunt ut labore et dolore magna aliqua. Ut enim ad minim veniam, quis nostrud exercitation ullamco laboris nisi ut aliquip ex ea commodo consequat. Duis aute irure dolor in reprehenderit in voluptate velit esse cillum dolore eu fugiat nulla pariatur. Excepteur sint occaecat cupidatat non proident, sunt in culpa qui officia deserunt mollit anim id est laborum.</p>
      <p>Lorem ipsum dolor sit amet, consectetur adipisicing elit, sed do eiusmod tempor incididunt ut labore et dolore magna aliqua. Ut enim ad minim veniam, quis nostrud exercitation ullamco laboris nisi ut aliquip ex ea commodo consequat. Duis aute irure dolor in reprehenderit in voluptate velit esse cillum dolore eu fugiat nulla pariatur. Excepteur sint occaecat cupidatat non proident, sunt in culpa qui officia deserunt mollit anim id est laborum.</p>
      <p>Lorem ipsum dolor sit amet, consectetur adipisicing elit, sed do eiusmod tempor incididunt ut labore et dolore magna aliqua. Ut enim ad minim veniam, quis nostrud exercitation ullamco laboris nisi ut aliquip ex ea commodo consequat. Duis aute irure dolor in reprehenderit in voluptate velit esse cillum dolore eu fugiat nulla pariatur. Excepteur sint occaecat cupidatat non proident, sunt in culpa qui officia deserunt mollit anim id est laborum.</p>
      <p>Lorem ipsum dolor sit amet, consectetur adipisicing elit, sed do eiusmod tempor incididunt ut labore et dolore magna aliqua. Ut enim ad minim veniam, quis nostrud exercitation ullamco laboris nisi ut aliquip ex ea commodo consequat. Duis aute irure dolor in reprehenderit.</p>
      <p class="closing">Yours Sincerely,</p>
    </section>

    <div class="signature" role="img" aria-label="Handwritten signature of the sender"></div>

    <div class="accent-area" role="img" aria-label="Soft decorative pattern of pale green and blue squares"></div>
  </main>
</body>
</html>
```